Moravel Aesthetic Doctor

I require an elegant, luxurious looking business card for my aesthetic business. I am a doctor and that will set me aside from competitors. I am planning to provide home and spa based treatments to clients with high expectations. I have attached my logo.

```html
<!DOCTYPE html>
<html lang="en">
<head>
<meta charset="utf-8">
<title>Moravel Aesthetic Doctor – Business Card</title>
<link href="https://fonts.googleapis.com/css2?family=Cormorant+Garamond:wght@400;500&family=Poppins:wght@300;400;500&display=swap" rel="stylesheet">
<style>
  :root {
    --stage: #d9dadc;
    --card: #23272b;
    --card-deep: #1d2024;
    --ghost: rgba(255,255,255,0.05);
    --silver: #b9bdc2;
    --white: #f1f2f4;
    --sky: #5bb8ea;
    --muted: #c9ccd0;
  }
  * { margin: 0; padding: 0; box-sizing: border-box; }
  html, body { width: 1200px; height: 800px; overflow: hidden; background: var(--stage); }
  .canvas {
    width: 1200px; height: 800px;
    display: flex; align-items: center; justify-content: center; gap: 40px;
  }
  .card {
    position: relative; width: 540px; height: 310px;
    border-radius: 22px; overflow: hidden;
    background: radial-gradient(circle at 30% 40%, var(--card) 0%, var(--card-deep) 100%);
    box-shadow: 0 16px 40px rgba(0,0,0,0.25);
  }
  .ghost-ring {
    position: absolute; border-radius: 50%;
    border: 14px solid var(--ghost);
  }
  .card-front .ghost-ring { width: 360px; height: 360px; left: -70px; top: 40px; }
  .card-back .ghost-ring { width: 380px; height: 380px; right: -90px; top: -40px; }

  .brand { display: flex; align-items: center; gap: 14px; position: absolute; }
  .brand-dot {
    width: 58px; height: 58px; border-radius: 50%;
    border: 2px solid var(--silver); flex-shrink: 0;
  }
  .brand-name {
    font-family: "Cormorant Garamond", serif; font-weight: 400;
    color: var(--silver); letter-spacing: 4px; line-height: 1; white-space: nowrap;
  }
  .brand-tag {
    font-family: "Cormorant Garamond", serif; font-weight: 500;
    color: var(--sky); letter-spacing: 2px; text-transform: uppercase; margin-top: 4px; white-space: nowrap;
  }
  .card-front .brand { left: 170px; top: 60px; }
  .card-front .brand-name { font-size: 42px; }
  .card-front .brand-tag { font-size: 16px; }

  .card-back .brand-stack { position: absolute; left: 28px; bottom: 36px; }
  .card-back .brand-name { font-size: 36px; }
  .card-back .brand-tag { font-size: 14px; }

  .details {
    position: absolute; left: 246px; top: 40px; right: 20px;
    font-family: "Poppins", sans-serif;
  }
  .doctor-name { color: var(--white); font-size: 21px; font-weight: 500; white-space: nowrap; }
  .doctor-name .postnominals { color: var(--sky); font-size: 10px; font-weight: 400; margin-left: 4px; }
  .qualification { color: var(--sky); font-size: 10.5px; font-weight: 300; margin-top: 2px; white-space: nowrap; }
  .rule { height: 1px; background: var(--sky); margin: 10px 0 12px; }
  .contact { list-style: none; }
  .contact li {
    display: flex; align-items: center; gap: 8px;
    color: var(--white); font-size: 11.5px; font-weight: 300; margin-bottom: 4px;
  }
  .contact-icon {
    width: 16px; height: 16px; border-radius: 50%; background: var(--sky);
    display: flex; align-items: center; justify-content: center; flex-shrink: 0;
  }
  .services { margin-top: 12px; color: var(--muted); font-size: 10px; font-weight: 300; line-height: 1.6; white-space: nowrap; }
</style>
</head>
<body>
<main class="canvas">

  <section class="card card-front" aria-label="Card front">
    <div class="ghost-ring"></div>
    <div class="brand">
      <div class="brand-dot"></div>
      <div>
        <div class="brand-name">MORAVEL</div>
        <div class="brand-tag">Aesthetic Doctor</div>
      </div>
    </div>
  </section>

  <section class="card card-back" aria-label="Card back">
    <div class="ghost-ring"></div>
    <div class="brand-stack">
      <div class="brand-name">MORAVEL</div>
      <div class="brand-tag">Aesthetic Doctor</div>
    </div>
    <div class="details">
      <h1 class="doctor-name">Dr Elena Varsk<span class="postnominals">MRCPCH MD</span></h1>
      <p class="qualification">Australasian Diploma of Aesthetic Medicine</p>
      <div class="rule"></div>
      <ul class="contact">
        <li>
          <span class="contact-icon"><svg width="9" height="9" viewBox="0 0 24 24"><path fill="#1d2024" d="M6.6 10.8a15 15 0 0 0 6.6 6.6l2.2-2.2a1 1 0 0 1 1-.25 11.4 11.4 0 0 0 3.6.57 1 1 0 0 1 1 1V20a1 1 0 0 1-1 1A17 17 0 0 1 3 4a1 1 0 0 1 1-1h3.5a1 1 0 0 1 1 1c0 1.25.2 2.45.57 3.57a1 1 0 0 1-.25 1z"/></svg></span>
          0800 555 019
        </li>
        <li>
          <span class="contact-icon"><svg width="9" height="9" viewBox="0 0 24 24"><path fill="#1d2024" d="M2 5h20v14H2z M3 6l9 7 9-7" stroke="#5bb8ea" stroke-width="1.5"/></svg></span>
          elena@moravel.co.nz
        </li>
        <li>
          <span class="contact-icon"><svg width="10" height="10" viewBox="0 0 24 24" fill="none" stroke="#1d2024" stroke-width="2"><circle cx="12" cy="12" r="9"/><path d="M3 12h18M12 3c3 3 3 15 0 18M12 3c-3 3-3 15 0 18"/></svg></span>
          www.moravel.co.nz
        </li>
      </ul>
      <p class="services">
        Dermal injectables - Plasma facials - Microneedling<br>
        Skin boosters - Excessive sweating<br>
        Home and Spa Based Treatments
      </p>
    </div>
  </section>

</main>
</body>
</html>
```